Business Card Design for Software Development Company

I am looking for a business card design the incorporates my new logo (attached below).

Key information to include:
Name: Martin Quelbrook
Title: CEO
Email: martin@brightwellcivic.example
Phone: 555-218-9403
Website: www.brightwellcivic.example

NOTE: This design should be easy to edit so that we can order cards for different members of our team.

```html
<!DOCTYPE html>
<html lang="en">
<head>
<meta charset="utf-8">
<title>BrightwellLabs Business Card</title>
<link rel="stylesheet" href="https://fonts.googleapis.com/css2?family=Montserrat:wght@400;600;700&display=swap">
<style>
  :root {
    --stage: #e4e5e8;
    --paper: #ffffff;
    --navy: #363f57;
    --navy-card: #394259;
    --ink: #2b2f3a;
    --white: #ffffff;
    --accent: #1aa88f;
  }
  * { box-sizing: border-box; margin: 0; padding: 0; }
  html, body { width: 1200px; height: 1059px; overflow: hidden; }
  body {
    background: var(--stage);
    font-family: "Montserrat", Arial, sans-serif;
    position: relative;
  }
  .card {
    position: absolute;
    overflow: hidden;
    box-shadow: 0 10px 24px rgba(0,0,0,0.25);
  }
  .card-front { left: 256px; top: 100px; width: 688px; height: 391px; background: var(--paper); }
  .card-back { left: 253px; top: 537px; width: 694px; height: 394px; background: var(--navy-card); }

  .brand {
    position: absolute;
    left: 0; right: 0;
    display: flex;
    justify-content: center;
  }
  .brand-inner { display: flex; flex-direction: column; }
  .brand-row { display: flex; align-items: center; gap: 12px; }
  .brand-mark { width: 32px; height: 32px; background: var(--accent); flex: none; }
  .brand-name {
    font-weight: 600;
    font-size: 58px;
    letter-spacing: -1.5px;
    line-height: 1;
    white-space: nowrap;
  }
  .brand-tagline {
    align-self: flex-end;
    font-weight: 700;
    font-size: 8.5px;
    letter-spacing: 0.4px;
    margin-top: 6px;
    text-transform: uppercase;
    white-space: nowrap;
  }
  .card-front .brand { top: 82px; }
  .card-front .brand-name, .card-front .brand-tagline { color: var(--navy); }

  .card-back .brand { top: 160px; }
  .card-back .brand-mark { width: 36px; height: 36px; }
  .card-back .brand-name { font-size: 64px; }
  .card-back .brand-tagline { font-size: 9px; }
  .card-back .brand-name, .card-back .brand-tagline { color: var(--white); }

  .person {
    position: absolute;
    right: 371px;
    top: 258px;
    text-align: right;
  }
  .person-name {
    font-weight: 600;
    font-size: 26px;
    color: var(--navy);
    text-transform: uppercase;
    letter-spacing: 0.2px;
    line-height: 1;
    white-space: nowrap;
  }
  .person-title {
    font-weight: 400;
    font-size: 18px;
    color: var(--ink);
    margin-top: 4px;
    line-height: 1.1;
  }
  .divider {
    position: absolute;
    left: 344px;
    top: 243px;
    width: 1.5px;
    height: 78px;
    background: var(--ink);
  }
  .contact-list {
    position: absolute;
    left: 370px;
    top: 235px;
    list-style: none;
  }
  .contact-item {
    display: flex;
    align-items: center;
    gap: 9px;
    height: 30.5px;
    font-size: 16px;
    color: var(--ink);
    letter-spacing: 0.3px;
    white-space: nowrap;
  }
  .contact-icon { width: 13px; height: 13px; fill: var(--ink); flex: none; }
</style>
</head>
<body>
  <section class="card card-front">
    <div class="brand">
      <div class="brand-inner">
        <div class="brand-row">
          <span class="brand-mark"></span>
          <span class="brand-name">BrightwellLabs</span>
        </div>
        <span class="brand-tagline">A division of Brightwell Civic</span>
      </div>
    </div>

    <div class="person">
      <p class="person-name">Martin Quelbrook</p>
      <p class="person-title">CEO</p>
    </div>
    <div class="divider"></div>

    <ul class="contact-list">
      <li class="contact-item">
        <svg class="contact-icon" viewBox="0 0 24 24"><path d="M6.6 10.8a15.1 15.1 0 0 0 6.6 6.6l2.2-2.2c.3-.3.7-.4 1-.2 1.1.4 2.3.6 3.6.6.6 0 1 .4 1 1V20c0 .6-.4 1-1 1A17 17 0 0 1 3 4c0-.6.4-1 1-1h3.5c.6 0 1 .4 1 1 0 1.3.2 2.5.6 3.6.1.3 0 .7-.2 1z"/></svg>
        <span>555-218-9403</span>
      </li>
      <li class="contact-item">
        <svg class="contact-icon" viewBox="0 0 24 24"><path d="M2 5h20v2l-10 6L2 7z"/><path d="M2 9l10 6 10-6v10H2z"/></svg>
        <span>martin@brightwellcivic.example</span>
      </li>
      <li class="contact-item">
        <svg class="contact-icon" viewBox="0 0 24 24"><circle cx="12" cy="12" r="10" fill="none" stroke="#2b2f3a" stroke-width="2"/><ellipse cx="12" cy="12" rx="4.5" ry="10" fill="none" stroke="#2b2f3a" stroke-width="1.8"/><path d="M2 12h20M4 7h16M4 17h16" stroke="#2b2f3a" stroke-width="1.6"/></svg>
        <span>www.brightwellcivic.example</span>
      </li>
    </ul>
  </section>

  <section class="card card-back">
    <div class="brand">
      <div class="brand-inner">
        <div class="brand-row">
          <span class="brand-mark"></span>
          <span class="brand-name">BrightwellLabs</span>
        </div>
        <span class="brand-tagline">A division of Brightwell Civic</span>
      </div>
    </div>
  </section>
</body>
</html>
```